We need a new label.

The idea is to have Harrowdale Estate across the top of the label.

Then have a HE in the center of the label in the font liberty cursive capital letters.

The brand name is "Mill Creek" Shiraz

The must have across the bottom of the label are:

750ml

Wine of Australia

Note:
We are thinking a black background with silver script. (we are not married to this)
However due to the price point we can not use foil.

The ultimate goal is to present this wine as authentically Australian with a goal of presenting Australia as clean, green and friendly.

```html
<!DOCTYPE html>
<html lang="en">
<head>
<meta charset="utf-8">
<title>Harrowdale Estate – Mill Creek Shiraz Label</title>
<link rel="stylesheet" href="https://fonts.googleapis.com/css2?family=Oswald:wght@300;400&family=Source+Sans+3:wght@700&family=Courgette&display=swap">
<style>
  :root {
    --bottle-edge: #000000;
    --bottle-mid: #2a2929;
    --label-red: #922a20;
    --wing-black: #050505;
    --gold: #e0aa2a;
    --white: #ffffff;
    --rust: #c26a4e;
  }
  * { margin: 0; padding: 0; box-sizing: border-box; }
  html, body { width: 919px; height: 1200px; overflow: hidden; }
  body {
    background: linear-gradient(90deg, var(--bottle-edge) 0%, var(--bottle-mid) 50%, var(--bottle-edge) 100%);
    position: relative;
  }
  .label {
    position: absolute;
    left: 162px;
    top: 227px;
    width: 613px;
    height: 735px;
  }
  .label-shape { position: absolute; inset: 0; overflow: visible; }
  .wing-ornament { position: absolute; left: 0; top: 0; width: 613px; height: 390px; }
  .estate-name {
    position: absolute;
    left: 0; right: 0; top: 160px;
    text-align: center;
    font-family: "Source Sans 3", sans-serif;
    font-weight: 700;
    font-size: 34px;
    letter-spacing: 0.03em;
    color: var(--gold);
    text-transform: uppercase;
  }
  .seal {
    position: absolute;
    left: 193px; top: 202px;
    width: 230px; height: 230px;
    border-radius: 50%;
    background: var(--wing-black);
  }
  .wine-name {
    position: absolute;
    left: 0; right: 0;
    text-align: center;
    text-transform: uppercase;
    font-family: "Oswald", sans-serif;
    font-weight: 400;
    line-height: 1;
  }
  .wine-name--brand { top: 455px; font-size: 56px; color: var(--gold); }
  .wine-name--variety { top: 522px; font-size: 45px; color: var(--white); }
  .volume {
    position: absolute;
    left: 0; right: 0; top: 606px;
    text-align: center;
    font-family: "Courgette", cursive;
    font-size: 46px;
    line-height: 1;
    color: var(--white);
  }
  .origin {
    position: absolute;
    left: 0; right: 0; top: 680px;
    text-align: center;
    font-family: "Oswald", sans-serif;
    font-weight: 300;
    font-size: 23px;
    letter-spacing: 0.55em;
    padding-left: 0.55em;
    color: var(--rust);
    line-height: 1;
  }
</style>
</head>
<body>
  <main class="label">
    <svg class="label-shape" width="613" height="735" viewBox="0 0 613 735">
      <polygon points="0,0 613,0 613,735 108,735 0,627" fill="var(--label-red)" stroke="var(--white)" stroke-width="1.5"/>
      <polygon points="0,670 0,735 65,735" fill="var(--label-red)" stroke="var(--white)" stroke-width="1.5"/>
    </svg>
    <svg class="wing-ornament" role="img" aria-label="Spread wings ornament framing the estate seal" viewBox="0 0 613 390" preserveAspectRatio="none">
      <defs>
        <linearGradient id="wingFade" x1="0" y1="0" x2="0" y2="1">
          <stop offset="0" stop-color="var(--wing-black)" stop-opacity="0.85"/>
          <stop offset="1" stop-color="var(--label-red)" stop-opacity="0"/>
        </linearGradient>
      </defs>
      <rect x="0.75" y="0.75" width="611.5" height="389" fill="url(#wingFade)"/>
    </svg>
    <p class="estate-name">Harrowdale Estate</p>
    <div class="seal"></div>
    <h1 class="wine-name wine-name--brand">Mill Creek</h1>
    <h2 class="wine-name wine-name--variety">Shiraz</h2>
    <p class="volume">750ml</p>
    <p class="origin">Wine of Australia</p>
  </main>
</body>
</html>
```